Meadowlark Property Review is a leading provider of residential appraisal and home inspection products in S

I need a business card/logo designed that obviously describes my business. We are a residential appraisal and home inspection company in Springfield, MO. We offer residential appraisals, home inspection, pest inspection and radon gas measurement. We have been in business for 18 years and hold state certified residential appraisal licenses and OBREX certified home inspection licenses. I have a logo that I really like and will attach, but would be open to new suggestions. I like more modern designs than traditional and would like a two sided card with our services, licenses and qualifications on the back.

```html
<!DOCTYPE html>
<html lang="en">
<head>
<meta charset="utf-8">
<title>Meadowlark Property Review — Business Card</title>
<link rel="stylesheet" href="https://fonts.googleapis.com/css2?family=Open+Sans:wght@400;600;700&display=swap">
<style>
  :root {
    --page: #d9d9d9;
    --card: #030303;
    --strip: #121212;
    --orange: #f7941d;
    --bronze: #a27a45;
    --gold: #c8a25f;
  }
  * { margin: 0; padding: 0; box-sizing: border-box; }
  html, body { width: 1200px; height: 900px; overflow: hidden; }
  body {
    background: var(--page);
    font-family: "Open Sans", Arial, sans-serif;
    position: relative;
  }
  .card {
    position: absolute;
    left: 250px;
    width: 700px;
    height: 400px;
    background: var(--card);
    overflow: hidden;
    box-shadow: 0 6px 18px rgba(0,0,0,0.25);
  }
  .card--front { top: 35px; }
  .card--back { top: 465px; }

  .band-bronze, .band-orange { position: absolute; left: 0; width: 100%; }
  .band-bronze { height: 9px; bottom: 40px; background: var(--bronze); }
  .band-orange { height: 36px; bottom: 0; background: var(--orange); }

  .brand {
    position: absolute;
    display: flex;
    align-items: center;
    gap: 10px;
    color: var(--orange);
    font-weight: 700;
    font-size: 26px;
    letter-spacing: 0.5px;
    white-space: nowrap;
    z-index: 2;
  }
  .brand__mark { width: 16px; height: 16px; background: var(--orange); flex: none; }
  .card--front .brand { left: 50%; top: 160px; transform: translateX(-50%); }
  .card--back .brand { left: 36px; top: 150px; font-size: 24px; }

  .person {
    position: absolute;
    right: 36px;
    top: 85px;
    text-align: right;
  }
  .person__name { color: var(--gold); font-weight: 600; font-size: 17px; letter-spacing: 0.5px; }
  .person__title { color: var(--orange); font-size: 16px; margin-top: 2px; }

  .contact-strip {
    position: absolute;
    left: 0; right: 0;
    top: 175px;
    bottom: 49px;
    background: var(--strip);
    color: var(--orange);
    font-size: 15px;
    line-height: 1.45;
  }
  .contact-group { position: absolute; display: flex; flex-direction: column; gap: 4px; }
  .contact-group--address { left: 36px; top: 42px; }
  .contact-group--phones { left: 290px; top: 70px; }
  .contact-group--web { left: 450px; top: 96px; }
  .contact-line { display: flex; align-items: flex-start; gap: 8px; white-space: nowrap; }
  .contact-line svg { width: 12px; height: 12px; margin-top: 5px; flex: none; fill: var(--gold); }
  .contact-line svg.icon-pin { width: 11px; height: 14px; margin-top: 3px; }
</style>
</head>
<body>

<section class="card card--front" aria-label="Card front">
  <div class="brand"><span class="brand__mark"></span>Meadowlark Property Review</div>
  <div class="band-bronze"></div>
  <div class="band-orange"></div>
</section>

<section class="card card--back" aria-label="Card back">
  <div class="contact-strip">
    <div class="contact-group contact-group--address">
      <div class="contact-line">
        <svg class="icon-pin" viewBox="0 0 11 14"><path d="M5.5 0A5.5 5.5 0 0 0 0 5.5C0 9.5 5.5 14 5.5 14S11 9.5 11 5.5A5.5 5.5 0 0 0 5.5 0zm0 7.6a2.1 2.1 0 1 1 0-4.2 2.1 2.1 0 0 1 0 4.2z"/></svg>
        <span>1234, Address Goes Here,<br>Country Name, 123456</span>
      </div>
    </div>
    <div class="contact-group contact-group--phones">
      <div class="contact-line">
        <svg viewBox="0 0 12 12"><path d="M1 3.5C1 2 3 1 6 1s5 1 5 2.5V5H8.5V3.8H3.5V5H1zM2.5 6h7l1 5h-9z"/></svg>
        <span>123.456.7890</span>
      </div>
      <div class="contact-line">
        <svg viewBox="0 0 12 12"><path d="M3.5 0h5a1 1 0 0 1 1 1v10a1 1 0 0 1-1 1h-5a1 1 0 0 1-1-1V1a1 1 0 0 1 1-1zm.5 1.5v7h4v-7zM6 9.5a.8.8 0 1 0 0 1.6.8.8 0 0 0 0-1.6z"/></svg>
        <span>123.456.7890</span>
      </div>
    </div>
    <div class="contact-group contact-group--web">
      <div class="contact-line">
        <svg viewBox="0 0 12 12"><path d="M0 2h12v8H0zm1 1v.4l5 3.2 5-3.2V3zm0 1.6V9h10V4.6L6 7.8z"/></svg>
        <span>info@youremail.com</span>
      </div>
      <div class="contact-line">
        <svg viewBox="0 0 12 12"><path d="M4.6 8.8l-1 1a1.6 1.6 0 0 1-2.3-2.3l2-2a1.6 1.6 0 0 1 2.3 0l.7-.7a2.6 2.6 0 0 0-3.7 0l-2 2a2.6 2.6 0 0 0 3.7 3.7l1-1zM7.4 3.2l1-1a1.6 1.6 0 0 1 2.3 2.3l-2 2a1.6 1.6 0 0 1-2.3 0l-.7.7a2.6 2.6 0 0 0 3.7 0l2-2A2.6 2.6 0 0 0 7.7 1.5l-1 1z"/></svg>
        <span>www.website.com</span>
      </div>
    </div>
  </div>

  <div class="brand"><span class="brand__mark"></span>Meadowlark Property Review</div>

  <div class="person">
    <div class="person__name">DANIEL WHITFORD</div>
    <div class="person__title">Managing Director</div>
  </div>

  <div class="band-bronze"></div>
  <div class="band-orange"></div>
</section>

</body>
</html>
```